Marrowby Water Taxi and Transport Business Card

I need business cards for my new water taxi and freight transport business I have started here in Kodiak Alaska. Kodiak is a remote island in the middle of the gulf of Alaska. There are seven native villages around the island and Kodiak is the #2 fishing port in the United States. We also have the largest Coast Guard Base in the U.S. My company will be providing water taxi and freight transport logistics to the villages and many hunting and fishing lodges as well as remote properties around the island.

I would like a business card that isn't status quo, something that stands out, either in feel or appearance. I do like clean minimal designs but it needs to have the necessary contact info on it.

Target Market(s)

remote lodge / property owners, residents of the many villages around Kodiak and any one wanting to enjoy the great outdoors of Kodiak Alaska

Industry/Entity Type

Business

Contact Information for Business Card

I like clean simple designs that aren't cluttered but still provide the necessary information

Colors
0255a3
3277b5
33a4d5
9bcb3c
add136
fbed22
ffc214
f78f20
f37122

Requirements
Must have
• logo and contact info
• Captain Mason Elwick
• www.marrowbyferryline.com
• mason@marrowbyferryline.com

```html
<!DOCTYPE html>
<html lang="en">
<head>
<meta charset="utf-8">
<title>Marrowby Water Taxi and Transport — Business Card</title>
<link href="https://fonts.googleapis.com/css2?family=Open+Sans:wght@400;600;700&display=swap" rel="stylesheet">
<style>
  :root {
    --stage: #3a3431;
    --card: #0c0c0d;
    --card-edge: #1a1a1b;
    --brand-blue: #3277b5;
    --accent-cyan: #33a4d5;
    --sun-orange: #f78f20;
    --text-light: #e6e6e6;
    --foil-silver: #c9c9c9;
  }
  * { box-sizing: border-box; margin: 0; padding: 0; }
  html, body {
    width: 1200px; height: 900px; overflow: hidden;
    background: var(--stage);
    font-family: "Open Sans", sans-serif;
  }
  .canvas {
    width: 1200px; height: 900px;
    display: flex; align-items: center; justify-content: center; gap: 60px;
  }
  .card {
    width: 525px; height: 300px;
    background: var(--card);
    border: 1px solid var(--card-edge);
    position: relative;
    overflow: hidden;
  }
  /* front face */
  .card-front { display: flex; align-items: center; }
  .brand-block {
    display: flex; align-items: center; gap: 8px;
    color: var(--brand-blue); font-weight: 700;
  }
  .card-front .brand-block {
    width: 250px; flex: none;
    padding: 50px 0 0 28px;
  }
  .brand-dot {
    width: 18px; height: 18px; border-radius: 50%;
    background: var(--sun-orange); flex: none;
  }
  .brand-name { line-height: 1.1; white-space: nowrap; }
  .brand-name .word { display: block; font-size: 30px; letter-spacing: 1px; }
  .brand-name .tagline { display: block; font-size: 11px; letter-spacing: .3px; }
  .divider {
    width: 1px; height: 130px; background: var(--accent-cyan); opacity: .8;
    flex: none;
  }
  .contact-block { padding-left: 26px; color: var(--text-light); min-width: 0; }
  .holder-name {
    color: var(--accent-cyan); font-weight: 700; font-size: 17px;
    margin-bottom: 34px; white-space: nowrap;
  }
  .contact-line {
    display: flex; align-items: center; gap: 8px;
    font-size: 12.5px; line-height: 1.5; white-space: nowrap;
  }
  .contact-line svg { width: 11px; height: 11px; fill: var(--accent-cyan); flex: none; }
  /* back face */
  .card-back {
    display: flex; align-items: center; justify-content: center;
  }
  .card-back .brand-block { color: var(--foil-silver); gap: 10px; }
  .card-back .brand-dot { width: 22px; height: 22px; background: var(--foil-silver); }
  .card-back .brand-name .word { font-size: 40px; }
  .card-back .brand-name .tagline { font-size: 13px; }
</style>
</head>
<body>
<main class="canvas">
  <section class="card card-front" aria-label="Card front">
    <div class="brand-block">
      <span class="brand-dot"></span>
      <span class="brand-name">
        <span class="word">MARROWBY</span>
        <span class="tagline">Water Taxi &amp; Transport</span>
      </span>
    </div>
    <div class="divider"></div>
    <div class="contact-block">
      <p class="holder-name">Captain Mason Elwick</p>
      <p class="contact-line">
        <svg viewBox="0 0 24 24" aria-hidden="true"><path d="M6.6 10.8a15.1 15.1 0 0 0 6.6 6.6l2.2-2.2a1 1 0 0 1 1-.25 11.4 11.4 0 0 0 3.6.57 1 1 0 0 1 1 1V20a1 1 0 0 1-1 1A17 17 0 0 1 3 4a1 1 0 0 1 1-1h3.5a1 1 0 0 1 1 1c0 1.25.2 2.450.57 3.57a1 1 0 0 1-.25 1z"/></svg>
        mason@marrowbyferryline.com
      </p>
      <p class="contact-line">
        <svg viewBox="0 0 24 24" aria-hidden="true"><path d="M2 5h20v14H2zm2 2v.5l8 5 8-5V7l-8 5z"/></svg>
        www.marrowbyferryline.com
      </p>
    </div>
  </section>

  <section class="card card-back" aria-label="Card back">
    <div class="brand-block">
      <span class="brand-dot"></span>
      <span class="brand-name">
        <span class="word">MARROWBY</span>
        <span class="tagline">Water Taxi &amp; Transport</span>
      </span>
    </div>
  </section>
</main>
</body>
</html>
```